Business Card for a New Zealand IT Startup

I need a business card for VELTA Holdings. We are a young startup based in New Zealand working in internet marketing and web development. The design should have some element connected to New Zealand, such as wave, koru or silver fern, just don't use a kiwi bird.

```html
<!DOCTYPE html>
<html lang="en">
<head>
<meta charset="utf-8">
<title>VELTA Holdings – Business Card</title>
<link rel="stylesheet" href="https://fonts.googleapis.com/css2?family=Open+Sans:wght@400;600;700&display=swap">
<style>
  :root {
    --page-bg: #e6e4e1;
    --card-bg: #1b1d20;
    --brand-blue: #1f7fd1;
    --brand-orange: #e8602a;
    --silver: #c9cbcd;
    --text-light: #f2f2f2;
    --divider: #d9d9d9;
  }
  * { box-sizing: border-box; margin: 0; padding: 0; }
  html, body { width: 1200px; height: 864px; overflow: hidden; }
  body {
    background: var(--page-bg);
    font-family: "Open Sans", Arial, sans-serif;
    position: relative;
  }
  .card {
    position: absolute;
    left: 260px;
    width: 680px;
    height: 388px;
    background: var(--card-bg);
    border-radius: 4px;
    overflow: hidden;
  }
  .card--front { top: 30px; }
  .card--back { top: 446px; }

  .brand {
    display: flex;
    align-items: center;
    gap: 14px;
    font-weight: 700;
    line-height: 1;
    white-space: nowrap;
  }
  .brand__dot { width: 20px; height: 20px; border-radius: 50%; flex: none; }

  .wave { position: absolute; fill: none; stroke-linecap: round; }

  /* Front */
  .card--front .brand {
    position: absolute;
    left: 90px;
    top: 120px;
    font-size: 46px;
    color: var(--silver);
    letter-spacing: 1px;
  }
  .card--front .brand__dot { background: var(--silver); }
  .card--front .wave { left: 90px; top: 186px; width: 380px; height: 30px; stroke: var(--silver); }
  .front-url {
    position: absolute;
    left: 92px;
    top: 236px;
    font-size: 16px;
    letter-spacing: 6px;
    color: var(--silver);
  }

  /* Back */
  .card--back .brand {
    position: absolute;
    left: 40px;
    top: 160px;
    font-size: 34px;
    color: var(--brand-blue);
  }
  .card--back .brand__dot { background: var(--brand-blue); width: 16px; height: 16px; }
  .card--back .wave { left: 40px; top: 210px; width: 300px; height: 26px; stroke: var(--brand-orange); }

  .divider {
    position: absolute;
    left: 380px;
    top: 60px;
    width: 2px;
    height: 268px;
    background: linear-gradient(to bottom, transparent, var(--divider) 30%, var(--divider) 70%, transparent);
  }

  .contact {
    position: absolute;
    left: 408px;
    top: 84px;
    color: var(--text-light);
    font-size: 17px;
    line-height: 1.3;
  }
  .contact__name { color: var(--brand-blue); font-weight: 700; font-size: 22px; letter-spacing: 0.5px; }
  .contact__title { color: var(--brand-orange); font-size: 16px; margin-bottom: 8px; }
  .contact__address { margin-bottom: 6px; }
  .contact__list { list-style: none; }
  .contact__item { display: flex; align-items: center; gap: 8px; }
  .contact__icon { width: 15px; height: 15px; fill: var(--brand-blue); flex: none; }
</style>
</head>
<body>

<section class="card card--front" aria-label="Card front">
  <div class="brand"><span class="brand__dot"></span>VELTA Holdings</div>
  <svg class="wave" viewBox="0 0 380 30" aria-hidden="true">
    <path d="M2 16 Q 49 2 96 16 T 190 16 T 284 16 T 378 16" stroke-width="2.5"/>
    <path d="M2 24 Q 49 12 96 24 T 190 24 T 284 24 T 378 24" stroke-width="1.2" opacity="0.6"/>
  </svg>
  <p class="front-url">www.veltaholdings.com</p>
</section>

<section class="card card--back" aria-label="Card back">
  <div class="brand"><span class="brand__dot"></span>VELTA Holdings</div>
  <svg class="wave" viewBox="0 0 300 26" aria-hidden="true">
    <path d="M2 13 Q 39 2 76 13 T 150 13 T 224 13 T 298 13" stroke-width="2.5"/>
    <path d="M2 21 Q 39 11 76 21 T 150 21 T 224 21 T 298 21" stroke-width="1.2" opacity="0.6"/>
  </svg>
  <div class="divider"></div>
  <div class="contact">
    <p class="contact__name">MARA TANE</p>
    <p class="contact__title">PRESIDENT</p>
    <p class="contact__address">412 Harbour Lane<br>Kelburn, Wellington 6012</p>
    <ul class="contact__list">
      <li class="contact__item">
        <svg class="contact__icon" viewBox="0 0 16 16"><path d="M3 1h3l1 4-2 1c1 2 3 4 5 5l1-2 4 1v3c0 1-1 2-2 2C7 15 1 9 1 3c0-1 1-2 2-2z"/></svg>
        021 480 3317
      </li>
      <li class="contact__item">
        <svg class="contact__icon" viewBox="0 0 16 16"><path d="M4 0h8a1 1 0 0 1 1 1v14a1 1 0 0 1-1 1H4a1 1 0 0 1-1-1V1a1 1 0 0 1 1-1zm1 2v10h6V2z"/></svg>
        027 615 9042
      </li>
      <li class="contact__item">
        <svg class="contact__icon" viewBox="0 0 16 16"><path d="M4 0h7v5H4zM1 6h14v8H1zm3 2v2h8V8z"/></svg>
        04 389 2270
      </li>
      <li class="contact__item">
        <svg class="contact__icon" viewBox="0 0 16 16"><path d="M0 3h16v1L8 9 0 4zm0 3 8 5 8-5v7H0z"/></svg>
        mara@veltaholdings.com
      </li>
      <li class="contact__item">
        <svg class="contact__icon" viewBox="0 0 16 16"><circle cx="8" cy="8" r="7"/></svg>
        www.veltaholdings.com
      </li>
    </ul>
  </div>
</section>

</body>
</html>
```